Business Card for Coastal Tundrabridge Advisory

We need a business card for Coastal Tundrabridge Advisory. The company website address is provided below. The company logo is attached. We provide specialized permafrost services to the mining, transportation, and oil & gas industries. The card should be prepared for:
Matthias Korhonen, PhD.
Coastal Tundrabridge Advisory
PO Box 418259
Quillwater, Alaska 99642
Direct: +1-907-555-0143
Email: mkorhonen@tundrabridgeadvisory.example
Website: www.coastaltundrabridgeadvisory.example

```html
<!DOCTYPE html>
<html lang="en">
<head>
<meta charset="utf-8">
<title>Coastal Tundrabridge Advisory – Business Card</title>
<link href="https://fonts.googleapis.com/css2?family=Roboto:wght@300;400;700&display=swap" rel="stylesheet">
<style>
  :root {
    --backdrop: #232323;
    --card: #111722;
    --ink: #ffffff;
    --ink-soft: #d9dde4;
    --deep-blue: #24346e;
    --rule: #8a909b;
  }
  * { margin: 0; padding: 0; box-sizing: border-box; }
  html, body {
    width: 1200px; height: 711px; overflow: hidden;
    background: var(--backdrop);
    font-family: "Roboto", Arial, sans-serif;
    color: var(--ink);
  }
  .stage {
    width: 1200px; height: 711px;
    display: flex; align-items: center; justify-content: center; gap: 40px;
  }
  .card {
    width: 540px; height: 309px;
    background: var(--card);
    position: relative;
    box-shadow: 0 10px 30px rgba(0,0,0,.5);
  }
  /* Back side */
  .card-back .brand-name {
    position: absolute; left: 0; right: 0; top: 104px;
    text-align: center;
    font-size: 30px; font-weight: 700; letter-spacing: 1px;
    color: var(--deep-blue);
    text-transform: uppercase;
    line-height: 1.15;
  }
  .card-back .services {
    position: absolute; left: 20px; right: 20px; bottom: 26px;
    text-align: center;
  }
  .services-title { font-size: 9px; font-weight: 700; letter-spacing: .3px; }
  .services-text { font-size: 9px; font-weight: 400; margin-top: 3px; color: var(--ink-soft); }
  /* Front side */
  .card-front .brand-name {
    position: absolute; left: 36px; top: 122px; width: 190px;
    font-size: 20px; font-weight: 700; letter-spacing: .5px;
    text-transform: uppercase; line-height: 1.2;
    color: var(--ink);
  }
  .card-front .divider {
    position: absolute; left: 262px; top: 60px; bottom: 60px;
    width: 1px; background: var(--rule);
  }
  .contact { position: absolute; left: 290px; top: 72px; right: 14px; }
  .person-name { font-size: 21px; line-height: 1.1; }
  .person-name .first { font-weight: 700; }
  .person-name .last { font-weight: 300; }
  .credential { font-size: 12px; font-weight: 700; margin-top: 2px; }
  .address { font-size: 9.5px; line-height: 1.4; margin-top: 12px; color: var(--ink-soft); }
  .lines { list-style: none; margin-top: 14px; }
  .lines li {
    display: flex; align-items: center; gap: 7px;
    font-size: 9.5px; line-height: 1.7; color: var(--ink-soft);
  }
  .lines svg { width: 10px; height: 10px; flex: none; }
</style>
</head>
<body>
<main class="stage">
  <section class="card card-back">
    <div class="brand-name">Coastal Tundrabridge<br>Advisory</div>
    <div class="services">
      <p class="services-title">OUR SERVICES</p>
      <p class="services-text">We provide specialized permafrost services to the mining, transportation, and oil &amp; gas industries</p>
    </div>
  </section>

  <section class="card card-front">
    <div class="brand-name">Coastal Tundrabridge Advisory</div>
    <div class="divider"></div>
    <div class="contact">
      <p class="person-name"><span class="first">Matthias</span> <span class="last">Korhonen</span></p>
      <p class="credential">PhD</p>
      <p class="address">PO Box 418259<br>Quillwater, Alaska 99642</p>
      <ul class="lines">
        <li>
          <svg viewBox="0 0 24 24" aria-hidden="true"><path fill="#fff" d="M6.6 10.8a15.1 15.1 0 0 0 6.6 6.6l2.2-2.2a1 1 0 0 1 1-.25 11.4 11.4 0 0 0 3.6.57 1 1 0 0 1 1 1V20a1 1 0 0 1-1 1A17 17 0 0 1 3 4a1 1 0 0 1 1-1h3.5a1 1 0 0 1 1 1c0 1.25.2 2.45.57 3.57a1 1 0 0 1-.25 1z"/></svg>
          +1-907-555-0143
        </li>
        <li>
          <svg viewBox="0 0 24 24" aria-hidden="true"><rect x="2" y="5" width="20" height="14" rx="1.5" fill="none" stroke="#fff" stroke-width="2"/><path d="M2.5 6l9.5 7 9.5-7" fill="none" stroke="#fff" stroke-width="2"/></svg>
          mkorhonen@tundrabridgeadvisory.example
        </li>
        <li>
          <svg viewBox="0 0 24 24" aria-hidden="true"><circle cx="12" cy="12" r="10" fill="none" stroke="#fff" stroke-width="2"/><path d="M2 12h20M12 2c3 3 3 17 0 20M12 2c-3 3-3 17 0 20" fill="none" stroke="#fff" stroke-width="1.6"/></svg>
          www.coastaltundrabridgeadvisory.example
        </li>
      </ul>
    </div>
  </section>
</main>
</body>
</html>
```